TALMORK

The business want a professional looking business card. We have a scetch we will add but want the extra upgrade, and would like more suggestions for variations of our business cards.

```html
<!DOCTYPE html>
<html lang="en">
<head>
<meta charset="utf-8">
<title>TALMORK Business Card</title>
<link rel="stylesheet" href="https://fonts.googleapis.com/css2?family=Montserrat:wght@400;500;700&display=swap">
<style>
  :root {
    --stage: #262626;
    --card: #161616;
    --card-soft: #1d1d1d;
    --gold: #d7a84a;
    --gold-light: #f1cf7a;
    --gold-deep: #a97a2a;
    --ink: #f2f2f2;
    --emboss: #2c2c2c;
  }
  * { margin: 0; padding: 0; box-sizing: border-box; }
  html, body {
    width: 1200px; height: 801px; overflow: hidden;
    background: var(--stage);
    font-family: "Montserrat", sans-serif;
  }
  .canvas {
    width: 1200px; height: 801px;
    display: flex; align-items: center; justify-content: center; gap: 40px;
  }
  .card {
    position: relative;
    width: 540px; height: 309px;
    border-radius: 16px;
    background: linear-gradient(135deg, var(--card-soft), var(--card));
    overflow: hidden;
    box-shadow: 0 18px 40px rgba(0,0,0,0.55);
  }
  /* Front */
  .gold-band {
    position: absolute; left: 0; right: 0; bottom: 0; height: 14px;
    background: linear-gradient(90deg, var(--gold-deep), var(--gold-light) 45%, var(--gold) 70%, var(--gold-deep));
  }
  .brand {
    position: absolute; left: 0; top: 0; width: 230px; height: 295px;
    display: flex; flex-direction: column; align-items: center; justify-content: center; gap: 16px;
  }
  .brand-dot {
    width: 34px; height: 34px; border-radius: 50%;
    background: var(--gold);
  }
  .brand-name {
    font-weight: 500; font-size: 26px; letter-spacing: 6px;
    color: var(--gold);
  }
  .divider {
    position: absolute; left: 232px; top: 95px; width: 1px; height: 120px;
    background: var(--gold-deep);
  }
  .details {
    position: absolute; left: 262px; top: 72px;
  }
  .person-name {
    font-weight: 700; font-size: 20px; color: var(--gold);
  }
  .person-role {
    font-weight: 400; font-size: 14px; color: var(--ink); margin-top: 4px;
  }
  .contact-list { list-style: none; margin-top: 26px; }
  .contact-item {
    display: flex; align-items: center; gap: 10px;
    font-size: 13px; color: var(--ink); margin-bottom: 10px;
  }
  .contact-icon { width: 14px; height: 14px; flex: none; }
  /* Back */
  .back { display: flex; align-items: center; justify-content: center; gap: 18px; }
  .back-dot {
    width: 44px; height: 44px; border-radius: 50%;
    background: var(--emboss);
  }
  .back-name {
    font-weight: 500; font-size: 44px; letter-spacing: 10px;
    color: var(--emboss);
  }
</style>
</head>
<body>
<main class="canvas">
  <section class="card front" aria-label="Business card front">
    <div class="brand">
      <span class="brand-dot"></span>
      <span class="brand-name">TALMORK</span>
    </div>
    <div class="divider"></div>
    <div class="details">
      <p class="person-name">Arne Kristian Dahlberg</p>
      <p class="person-role">CEO &amp; Founder</p>
      <ul class="contact-list">
        <li class="contact-item">
          <svg class="contact-icon" viewBox="0 0 24 24"><path fill="#d7a84a" d="M6.6 10.8a15 15 0 0 0 6.6 6.6l2.2-2.2c.3-.3.7-.4 1-.2 1.1.4 2.3.6 3.6.6.6 0 1 .4 1 1V20c0 .6-.4 1-1 1A17 17 0 0 1 3 4c0-.6.4-1 1-1h3.5c.6 0 1 .4 1 1 0 1.2.2 2.4.6 3.6.1.3 0 .7-.2 1z"/></svg>
          004795550142
        </li>
        <li class="contact-item">
          <svg class="contact-icon" viewBox="0 0 24 24"><path fill="#d7a84a" d="M3 5h18v14H3z"/><path fill="none" stroke="#161616" stroke-width="1.8" d="M3 6l9 7 9-7"/></svg>
          talmork.llc@mailhub.com
        </li>
        <li class="contact-item">
          <svg class="contact-icon" viewBox="0 0 24 24"><circle cx="12" cy="12" r="10" fill="#d7a84a"/><path fill="none" stroke="#161616" stroke-width="1.5" d="M2 12h20M12 2c3 3 3 17 0 20M12 2c-3 3-3 17 0 20"/></svg>
          www.talmork.studio
        </li>
      </ul>
    </div>
    <div class="gold-band"></div>
  </section>

  <section class="card back" aria-label="Business card back">
    <span class="back-dot"></span>
    <span class="back-name">TALMORK</span>
  </section>
</main>
</body>
</html>
```